Halvik - consultancy website

I need a new design for my webpage/presence [to be functioning with Wordpress - I have a programmer to set it up but not the design idea].
My company is Halvik - a consultancy firm focused on growth management for Swedish SME's primarily;. We call it Leadership toolkit for firms on the rise, kind of a doctor helping small become big. Contentwise, its a simple frontpage + 3-4 subpages with content re company/myself/focus etc. The new site should communicate a fresh, trustworthy take yet simple and functional on all devices [i.e. think UI compatible for mobile/tablet]. Current building parts/form elements are
a) existing logo and text elements
b) existing pictures
c) the yellowish color
colours and new ideas on pictures/positioning are welcome. I prefer a 'full width page' solution with centralised text elements but that's all up to you to suggest. Current site is a quickfix made by myself - now I'm moving it to a new platform so want to take the opportunity to make it
Nothing superspecial as it is a 2-man show; on the other hand I still want to have a modern & fresh reflection of my brand in digital environments. Help me out!
www.halvik-demo.se
Best
Lina Bergqvist

```html
<!DOCTYPE html>
<html lang="en">
<head>
<meta charset="utf-8">
<title>Halvik – Growth management consultancy</title>
<link href="https://fonts.googleapis.com/css2?family=Arimo:ital,wght@0,400;0,700;1,400&family=PT+Serif&display=swap" rel="stylesheet">
<style>
:root{
  --orange:#f0a33a;
  --orange-dark:#a8721f;
  --peach:#f7d5a0;
  --ink:#1b1b1b;
  --text:#444;
  --muted:#8a8a8a;
  --footer:#1c1c1c;
  --footer-bottom:#121212;
  --band:#2a2530;
  --red:#d9312b;
  --fb:#3b5998;
  --tw:#3fa9e0;
  --gp:#dd4b39;
}
*{box-sizing:border-box;margin:0;padding:0}
html,body{width:750px;height:1200px;overflow:hidden}
body{font-family:"Arimo",Arial,sans-serif;color:var(--text);background:#fff;position:relative}
.abs{position:absolute}

/* header */
.header-left{left:0;top:0;width:278px;height:72px;background:#f8f8f8}
.header-right{left:278px;top:0;width:472px;height:72px;background:var(--peach)}
.brand{left:62px;top:12px;font-family:"PT Serif",serif;font-size:31px;color:var(--ink);line-height:1}
.tagline{left:63px;top:44px;font-family:"PT Serif",serif;font-size:9px;color:var(--ink)}
.nav{left:420px;top:30px;display:flex;gap:22px;font-size:9px;font-weight:700;color:var(--ink)}
.nav a{color:inherit;text-decoration:none;position:relative}
.nav a.active{color:#c5741a}
.nav a.active::after{content:"";position:absolute;left:-12px;right:-12px;top:17px;height:2px;background:var(--orange)}

/* hero */
.hero-photo{left:0;top:72px;width:278px;height:298px;background:linear-gradient(180deg,#f2f2f2 0%,#e9e7e4 70%,#d9b79a 100%)}
.hero-panel{left:278px;top:72px;width:472px;height:298px;background:var(--orange)}
.hero-line{background:var(--orange-dark);color:#fff;font-weight:700;font-size:16px;padding:2px 5px;line-height:19px;right:69px}
.hero-btn{left:616px;top:326px;width:65px;height:20px;background:#000;color:#fff;font-size:9px;display:flex;align-items:center;justify-content:center}
.dots{left:707px;top:343px;display:flex;gap:3px}
.dots span{width:6px;height:6px;border-radius:50%;border:1px solid #222}
.dots span.on{background:#222}
.hero-shadow{left:0;top:370px;width:750px;height:14px;background:linear-gradient(#ececec,#fff)}

/* about */
.section-title{font-weight:700;color:var(--ink)}
.about-title{left:0;width:750px;top:411px;text-align:center;font-size:16px}
.about-text{left:66px;width:618px;top:443px;text-align:center;font-size:7px;line-height:14px;color:#333}
.btn-orange{left:337px;top:515px;width:75px;height:22px;background:var(--orange);color:#fff;font-size:8px;display:flex;align-items:center;justify-content:center}

/* testimonials */
.testimonials{left:0;top:581px;width:750px;height:225px;background:linear-gradient(180deg,#2c2a34 0%,#3a2e2a 60%,#4a3526 100%)}
.testi-title{left:0;width:750px;top:604px;text-align:center;color:#fff;font-size:16px;font-weight:700}
.avatar{left:345px;top:641px;width:64px;height:64px;border-radius:50%;background:radial-gradient(circle at 50% 45%,#9a9a9a,#4a4a4a 70%,#1e1e1e)}
.quote{font-size:44px;font-family:"PT Serif",serif;color:#bdbdbd;line-height:1}
.testi-text{left:150px;width:450px;top:719px;text-align:center;font-size:7.5px;font-style:italic;color:#e6e6e6;line-height:13px}
.testi-name{left:0;width:750px;top:766px;text-align:center;font-size:7px;color:#fff}
.testi-name b{font-weight:700}
.arrow-side{top:682px}

/* news */
.news-title{left:60px;top:835px;font-size:16px}
.news-arrow{top:836px;width:16px;height:14px;display:flex;align-items:center;justify-content:center}
.card{top:883px;width:220px;height:80px}
.card .thumb{position:absolute;left:0;top:0;width:98px;height:80px}
.card .info{position:absolute;left:107px;top:0;width:94px}
.card h3{font-size:7px;font-weight:400;color:var(--ink);line-height:11px}
.card .date{font-size:5.5px;color:#555;margin-top:3px;padding-bottom:3px;border-bottom:1px solid #ddd}
.card p{font-size:6px;line-height:9px;color:#555;margin-top:5px}
.card .more{font-size:6px;color:var(--red);margin-top:5px;display:flex;align-items:center;gap:4px}

/* footer */
.footer{left:0;top:1025px;width:750px;height:143px;background:var(--footer)}
.footer-bottom{left:0;top:1168px;width:750px;height:32px;background:var(--footer-bottom);color:#777;font-size:7px;text-align:center;line-height:32px}
.foot-h{font-size:9px;color:#ddd}
.divider{top:1052px;width:1px;height:98px;background:#333}
.social{top:1079px;width:45px;height:58px;color:#fff;font-size:8px;text-align:center}
.social .ring{width:24px;height:24px;border-radius:50%;background:rgba(255,255,255,.18);margin:9px auto 7px}
.mail-text{left:334px;top:1077px;width:150px;font-size:7px;line-height:12px;color:#999}
.mail-input{left:334px;top:1107px;width:127px;height:18px;background:#fff;font-size:6.5px;color:#aaa;padding-left:10px;line-height:18px}
.mail-go{left:461px;top:1107px;width:18px;height:18px;background:var(--orange);display:flex;align-items:center;justify-content:center}
.privacy{left:334px;top:1130px;font-size:6.5px;color:#777}
.menu-list{left:607px;top:1077px;list-style:none;font-size:7px;color:#ddd;line-height:13.5px}
</style>
</head>
<body>

<header>
  <div class="abs header-left"></div>
  <div class="abs header-right"></div>
  <div class="abs brand">Halvik.</div>
  <div class="abs tagline">Leadership toolkit for firms on the rise</div>
  <nav class="abs nav">
    <a class="active">Home</a><a>About Us</a><a>Services</a><a>Gallery</a><a>Contact Us</a>
  </nav>
</header>

<section class="hero">
  <div class="abs hero-photo" role="img" aria-label="Photo of a young girl looking up beside a wall height chart"></div>
  <div class="abs hero-panel"></div>
  <div class="abs hero-line" style="top:275px">We are a consultancy firm focused on growth</div>
  <div class="abs hero-line" style="top:298px">management for Swedish SME's</div>
  <div class="abs hero-btn">Read More</div>
  <div class="abs dots"><span class="on"></span><span></span><span></span></div>
  <div class="abs hero-shadow"></div>
</section>

<section class="about">
  <h2 class="abs section-title about-title">About Halvik</h2>
  <p class="abs about-text">Lorem ipsum dolor sit amet, consectetur adipiscing elit. Fusce tristique ultricies dui et porta. Sed luctus mauris at dictum auctor. Ut sit amet eleifend tortor, vel fermentum ante. Sed luctus tellus eget tortor mollis, in ullamcorper erat facilisis. Pellentesque bibendum nec nisi ut consectetur. Mauris et elit id est luctus dapibus laoreet scelerisque arcu. Nam varius tincidunt enim quis ultricies. Morbi eleifend, dui faucibus gravida pellentesque, dui lectus tristique ante, et tempor metus ante ut mauris. Quisque feugiat massa ut nisi iaculis pulvinar. Ut euismod mauris enim, ac ultrices massa dignissim ac.</p>
  <div class="abs btn-orange">View More</div>
</section>

<section class="testimonials-wrap">
  <div class="abs testimonials" role="img" aria-label="Night city skyline with a suspension bridge"></div>
  <h2 class="abs testi-title">Testimonials</h2>
  <div class="abs avatar" role="img" aria-label="Portrait of the client giving the testimonial"></div>
  <svg class="abs arrow-side" style="left:20px" width="14" height="28" viewBox="0 0 14 28"><path d="M13 1 1 14l12 13" fill="none" stroke="#ddd" stroke-width="1.2"/></svg>
  <svg class="abs arrow-side" style="left:716px" width="14" height="28" viewBox="0 0 14 28"><path d="M1 1l12 13L1 27" fill="none" stroke="#ddd" stroke-width="1.2"/></svg>
  <div class="abs quote" style="left:128px;top:695px">&ldquo;</div>
  <div class="abs quote" style="left:600px;top:748px">&rdquo;</div>
  <p class="abs testi-text">Mauris interdum velit leo, ac porta leo vehicula sed. Maecenas iaculis cursus magna. Vestibulum molestie, urna vel lobortis dictum, lacus nibh varius elit, ac tristique sapien dui sit amet diam. Phasellus hendrerit, augue vitae tristique rhoncus, felis urna blandit mauris, vel egestas ex tellus quis leo. Morbi at lacus in</p>
  <div class="abs testi-name"><b>Mats,</b> Lorme ipsum</div>
</section>

<section class="news">
  <h2 class="abs section-title news-title">Latest News</h2>
  <div class="abs news-arrow" style="left:654px;background:var(--orange)"><svg width="6" height="8" viewBox="0 0 6 8"><path d="M5 1 2 4l3 3" fill="none" stroke="#fff" stroke-width="1.2"/></svg></div>
  <div class="abs news-arrow" style="left:672px;background:#222"><svg width="6" height="8" viewBox="0 0 6 8"><path d="M1 1l3 3-3 3" fill="none" stroke="#fff" stroke-width="1.2"/></svg></div>

  <article class="abs card" style="left:61px">
    <div class="thumb" role="img" aria-label="Two businessmen reviewing a tablet" style="background:linear-gradient(135deg,#c9c4bd,#6d6257 60%,#3b3530)"></div>
    <div class="info">
      <h3>Lorem ipsum dolor sit amet, consectetur</h3>
      <div class="date">15/05/2016 &nbsp;- &nbsp;Friday</div>
      <p>Mauris interdum velit leo, ac porta leo vehicula sed. Maece-nas iaculis</p>
      <div class="more">Read More <svg width="7" height="7" viewBox="0 0 7 7"><circle cx="3.5" cy="3.5" r="3" fill="none" stroke="#d9312b" stroke-width=".8"/><path d="M2 3.5h3M3.8 2.3 5 3.5 3.8 4.7" fill="none" stroke="#d9312b" stroke-width=".8"/></svg></div>
    </div>
  </article>

  <article class="abs card" style="left:272px">
    <div class="thumb" role="img" aria-label="Business handshake over documents" style="background:linear-gradient(135deg,#dfe6ee,#7f93ab 55%,#2e3c52)"></div>
    <div class="info">
      <h3>Lorem ipsum dolor sit amet, consectetur</h3>
      <div class="date">15/05/2016 &nbsp;- &nbsp;Friday</div>
      <p>Mauris interdum velit leo, ac porta leo vehicula sed. Maece-nas iaculis</p>
      <div class="more">Read More <svg width="7" height="7" viewBox="0 0 7 7"><circle cx="3.5" cy="3.5" r="3" fill="none" stroke="#d9312b" stroke-width=".8"/><path d="M2 3.5h3M3.8 2.3 5 3.5 3.8 4.7" fill="none" stroke="#d9312b" stroke-width=".8"/></svg></div>
    </div>
  </article>

  <article class="abs card" style="left:483px">
    <div class="thumb" role="img" aria-label="Team silhouettes in a sunlit office" style="background:linear-gradient(180deg,#f3efe2,#c8b895 55%,#3a342c)"></div>
    <div class="info">
      <h3>Lorem ipsum dolor sit amet, consectetur</h3>
      <div class="date">15/05/2016 &nbsp;- &nbsp;Friday</div>
      <p>Mauris interdum velit leo, ac porta leo vehicula sed. Maece-nas iaculis</p>
      <div class="more">Read More <svg width="7" height="7" viewBox="0 0 7 7"><circle cx="3.5" cy="3.5" r="3" fill="none" stroke="#d9312b" stroke-width=".8"/><path d="M2 3.5h3M3.8 2.3 5 3.5 3.8 4.7" fill="none" stroke="#d9312b" stroke-width=".8"/></svg></div>
    </div>
  </article>
</section>

<footer>
  <div class="abs footer"></div>
  <div class="abs foot-h" style="left:61px;top:1050px">Let's Connect</div>
  <div class="abs social" style="left:61px;background:var(--fb)"><div class="ring"></div>2598</div>
  <div class="abs social" style="left:111px;background:var(--tw)"><div class="ring"></div>4576</div>
  <div class="abs social" style="left:161px;background:var(--gp)"><div class="ring"></div>1269</div>
  <div class="abs divider" style="left:273px"></div>

  <div class="abs foot-h" style="left:334px;top:1051px">Mailing List</div>
  <p class="abs mail-text">Sign up for our mailing list to get latest updates and offers.</p>
  <div class="abs mail-input">Email address</div>
  <div class="abs mail-go"><svg width="8" height="6" viewBox="0 0 8 6"><path d="M1 3l2 2 4-4" fill="none" stroke="#fff" stroke-width="1.3"/></svg></div>
  <div class="abs privacy">We respect your privacy</div>
  <div class="abs divider" style="left:546px"></div>

  <div class="abs foot-h" style="left:607px;top:1051px">Menu</div>
  <ul class="abs menu-list"><li>Home</li><li>About Us</li><li>Services</li><li>Gallery</li><li>Contact Us</li></ul>

  <div class="abs footer-bottom">© Copyrights 2015 All Rights Reserved</div>
</footer>

</body>
</html>
```